Business Card Design

We are looking for a business card designed for our landscaping company. We do landscaping installation & Maintenance Services. We would like to see designs that have basic landscaping in background. We also think it is important to have both of our names and phone numbers on the card. We need something that stands out a little whether it is shape of the card or thickness or design.

Business

Bramblewood Yardworks, bramblewoodyard@mailvista.net, Owen Platt 555-273-9104, Daniel Korbin 555-618-3927

```html
<!DOCTYPE html>
<html lang="en">
<head>
<meta charset="utf-8">
<title>Bramblewood Yardworks – Business Card</title>
<link rel="stylesheet" href="https://fonts.googleapis.com/css2?family=Old+Standard+TT:wght@700&family=Arimo:wght@400&display=swap">
<style>
  :root {
    --page-bg: #ecebe8;
    --card-white: #ffffff;
    --mist-green: #d9ecd0;
    --foliage-grey: #c9c9c9;
    --lawn-green: #67bd4b;
    --ink: #050505;
  }
  * { margin: 0; padding: 0; box-sizing: border-box; }
  html, body {
    width: 1189px;
    height: 1200px;
    overflow: hidden;
    background: var(--page-bg);
  }
  .business-card {
    position: absolute;
    left: 44px;
    top: 287px;
    width: 1100px;
    height: 626px;
    box-shadow: 0 6px 18px rgba(0, 0, 0, 0.18);
  }
  .business-card svg { display: block; width: 100%; height: 100%; }
  .company-name {
    font-family: "Old Standard TT", Georgia, serif;
    font-weight: 700;
    font-size: 68px;
    fill: var(--ink);
  }
  .contact-email, .partner-phone {
    font-family: "Arimo", Arial, sans-serif;
    font-weight: 400;
    fill: var(--ink);
  }
  .contact-email { font-size: 32px; }
  .partner-name {
    font-family: "Old Standard TT", Georgia, serif;
    font-weight: 700;
    font-size: 44px;
    fill: var(--ink);
  }
  .partner-phone { font-size: 33px; }
</style>
</head>
<body>
  <div class="business-card">
    <svg viewBox="0 0 1125 640" xmlns="http://www.w3.org/2000/svg">
      <defs>
        <linearGradient id="sky-wash" x1="0" y1="0" x2="0.6" y2="1">
          <stop offset="0" stop-color="#f3f8f0"/>
          <stop offset="1" stop-color="#ffffff"/>
        </linearGradient>
        <radialGradient id="mist-glow" cx="0.55" cy="0" r="0.5">
          <stop offset="0" stop-color="var(--mist-green)"/>
          <stop offset="1" stop-color="#ffffff" stop-opacity="0"/>
        </radialGradient>
        <radialGradient id="foliage-wash" cx="0.1" cy="0" r="0.9">
          <stop offset="0" stop-color="var(--foliage-grey)" stop-opacity="0.75"/>
          <stop offset="1" stop-color="var(--foliage-grey)" stop-opacity="0"/>
        </radialGradient>
      </defs>

      <rect class="card-face" width="1125" height="640" fill="url(#sky-wash)"/>
      <rect class="mist-glow" x="300" y="0" width="825" height="240" fill="url(#mist-glow)"/>
      <rect class="foliage-corner" x="0" y="0" width="380" height="220" fill="url(#foliage-wash)"
            role="img" aria-label="Faint grey bamboo leaves hanging from the top-left corner"/>

      <text class="company-name" x="571" y="198" text-anchor="middle">Bramblewood Yardworks</text>
      <text class="contact-email" x="584" y="287" text-anchor="middle">bramblewoodyard@mailvista.net</text>

      <path class="wave-band" fill="var(--ink)"
            d="M0,323 C200,365 420,375 620,335 C820,295 960,290 1125,350 L1125,378
               C950,320 820,335 620,380 C420,420 200,420 0,388 Z"/>
      <path class="lawn-field" fill="var(--lawn-green)"
            d="M0,388 C200,420 420,420 620,380 C820,335 950,320 1125,378 L1125,640 L0,640 Z"/>

      <text class="partner-name" x="181" y="511">Owen Platt</text>
      <text class="partner-phone" x="212" y="561">555-273-9104</text>

      <line class="partner-divider" x1="564" y1="456" x2="564" y2="593" stroke="var(--ink)" stroke-width="3"/>

      <text class="partner-name" x="672" y="511">Daniel Korbin</text>
      <text class="partner-phone" x="669" y="561">555-618-3927</text>
    </svg>
  </div>
</body>
</html>
```